International oil and gas consultancy needs a business card design

We need a business card design for a new oil and gas consultancy business based in Perth Australia. This is a professional services business and needs a moderately conservative type of business card. The business card also needs to be simple and uncluttered. The colour of the business logo is dark red (see attached file).
The front of the card should have a white background and mainly black lettering and perhaps some use of dark red and/or grey (your choice).
The back of the card should have a light grey background with dark red, black and or both dark red & black lettering (your choice).
Please find attached a clear brief of how I would like the business card designed.
Updates

Hello Everyone, I have slightly modified the brief. The main change is to incorporate some dark red and grey colours into the card, while still keeping the black lettering dominant. I have made the changes in the attached detailed brief document. Regards

Please note, the front of the card must say Harbour Ledger Services (in addition to the logo).

Industry/Entity Type

Conservative

Requirements
Must have
• brief has been updated. please refer to attachment for details.

Front of the card MUST say Harbour Ledger Services (in addition to the logo)

```html
<!DOCTYPE html>
<html lang="en">
<head>
<meta charset="utf-8">
<title>Harbour Ledger Services – Business Card</title>
<link rel="stylesheet" href="https://fonts.googleapis.com/css2?family=Arimo:wght@400;700&display=swap">
<style>
  :root {
    --stage: #d9d9db;
    --card: #ffffff;
    --ink: #111111;
    --brand-red: #8c1c22;
    --shadow: rgba(0, 0, 0, 0.28);
  }
  * { margin: 0; padding: 0; box-sizing: border-box; }
  html, body {
    width: 1200px;
    height: 599px;
    overflow: hidden;
  }
  body {
    background: var(--stage);
    font-family: "Arimo", Arial, sans-serif;
    color: var(--ink);
  }
  .card-sheet {
    width: 1200px;
    height: 599px;
    display: flex;
    align-items: center;
    justify-content: center;
    gap: 60px;
  }
  .card {
    position: relative;
    width: 500px;
    height: 290px;
    background: var(--card);
    box-shadow: 4px 6px 14px var(--shadow);
  }
  .brand-name {
    position: absolute;
    left: 30px;
    top: 52px;
    display: flex;
    align-items: center;
    gap: 10px;
    font-size: 22px;
    font-weight: 700;
    color: var(--brand-red);
    letter-spacing: 0.2px;
  }
  .brand-mark {
    width: 14px;
    height: 14px;
    background: var(--brand-red);
  }
  /* Front */
  .holder {
    position: absolute;
    right: 30px;
    top: 102px;
    text-align: right;
    font-size: 13px;
    line-height: 1.3;
  }
  .holder-name {
    font-size: 19px;
    font-weight: 700;
    margin-bottom: 4px;
  }
  .contact {
    position: absolute;
    right: 30px;
    top: 200px;
    text-align: right;
    font-size: 13px;
    line-height: 1.4;
    list-style: none;
  }
  /* Back */
  .tagline {
    position: absolute;
    left: 30px;
    top: 118px;
    font-size: 14px;
    line-height: 1.35;
  }
  .services {
    position: absolute;
    left: 300px;
    top: 178px;
    list-style: none;
    font-size: 14px;
    line-height: 1.65;
  }
  .services li {
    display: flex;
    align-items: center;
    gap: 14px;
  }
  .services li::before {
    content: "";
    width: 8px;
    height: 8px;
    border-radius: 50%;
    background: var(--ink);
  }
</style>
</head>
<body>
  <main class="card-sheet">
    <section class="card card-front" aria-label="Card front">
      <div class="brand-name"><span class="brand-mark"></span>Harbour Ledger Services</div>
      <div class="holder">
        <p class="holder-name">Neil Brandt</p>
        <p class="holder-role">Director</p>
        <p class="holder-region">Australasia and South East Asia</p>
      </div>
      <ul class="contact">
        <li>+61 (0)400 318 925</li>
        <li>neil@harbourledger.com</li>
        <li>www.harbourledger.com</li>
      </ul>
    </section>

    <section class="card card-back" aria-label="Card back">
      <div class="brand-name"><span class="brand-mark"></span>Harbour Ledger Services</div>
      <p class="tagline">Specialist Financial Consultants<br>to the Oil and Gas Industry</p>
      <ul class="services">
        <li>Joint Venture Audits</li>
        <li>Contract Audits</li>
        <li>Operational Audits</li>
      </ul>
    </section>
  </main>
</body>
</html>
```